Webdesign für Gemeinschaftspraxis (13820)
Zielgruppe
Die Website ist für eine fachärztliche Gemeinschaftspraxis, die sich aus Internisten, Betriebsmedizinern, Präventionsärzten, Kardiologen, Allgemeinmedizinern und Phlebologen zusammensetzt.
Die Zielgruppe sind bestehende Patienten sowie potentielle Patienten.
Die Website soll informativ sein.
Aufgabenstellung
Die Website soll in schlichten Farben gehalten sein, die zum Logo und zu den Fotos passen.
Die Website soll als kurzer, informativer Auftritt dienen
Die gelieferten Fotos sollen verwendet werden.
Es soll eine Onepage-Website werden, die so aufgebaut ist, wie die Website unter dem folgenden Link: https://www.ihr-weg-zum-ziel-online.de/

```html
<!DOCTYPE html>
<html lang="de">
<head>
<meta charset="utf-8">
<title>Leistungen – Praxis Lindenhof</title>
<link rel="stylesheet" href="https://fonts.googleapis.com/css2?family=Fira+Sans:wght@400;500&family=Roboto:wght@400&display=swap">
<style>
  :root {
    --page-bg: #e4e4e4;
    --header-bg: #ffffff;
    --ink: #111111;
    --brand: #1a2244;
    --row-bg: #545454;
    --row-text: #ffffff;
    --panel-bg: #ffffff;
    --panel-title: #444444;
    --panel-text: #7a7a7a;
  }
  * { box-sizing: border-box; margin: 0; padding: 0; }
  html, body {
    width: 1200px; height: 793px; overflow: hidden;
    background: var(--page-bg);
    font-family: "Roboto", sans-serif;
  }
  .site-header {
    position: absolute; left: 0; top: 0; width: 1200px; height: 51px;
    background: var(--header-bg);
    box-shadow: 0 2px 12px rgba(0,0,0,0.08);
    z-index: 2;
  }
  .brand {
    position: absolute; left: 228px; top: 14px;
    display: flex; align-items: center; gap: 6px;
    font-family: "Fira Sans", sans-serif; font-weight: 500;
    font-size: 11px; letter-spacing: 0.04em; color: var(--brand);
  }
  .brand-mark { width: 14px; height: 14px; background: var(--brand); }
  .main-nav a {
    position: absolute; top: 16px; height: 18px; line-height: 18px;
    font-size: 8.5px; letter-spacing: 0.28em; color: var(--ink);
    text-decoration: none; white-space: nowrap;
  }
  .main-nav a.is-active {
    border: 1.2px solid var(--ink); padding: 0 10px; left: 416px; width: 83px;
    line-height: 16px; text-align: center;
  }
  .page-title {
    position: absolute; left: 198px; top: 92px;
    font-weight: 400; font-size: 16.5px; letter-spacing: 0.14em; color: var(--ink);
  }
  .services {
    position: absolute; left: 198px; top: 126px; width: 558px;
    border: 1px solid #fff; border-bottom: none; list-style: none;
  }
  .service {
    height: 26px; border-bottom: 1px solid #fff;
    background: var(--row-bg); color: var(--row-text);
    font-family: "Fira Sans", sans-serif; font-size: 10.5px; letter-spacing: 0.09em;
    line-height: 25px; padding-left: 7px; white-space: nowrap;
  }
  .service.is-open {
    height: 110px; background: var(--panel-bg); color: var(--panel-title);
    line-height: normal; padding: 8px 7px 0;
  }
  .service-body {
    margin-top: 8px; width: 470px; white-space: normal;
    font-family: "Roboto", sans-serif; font-size: 9px; line-height: 14px;
    letter-spacing: 0; color: var(--panel-text);
  }
  .page-end {
    position: absolute; left: 0; top: 779px; width: 1200px; height: 14px;
    background: #ffffff;
  }
</style>
</head>
<body>
  <header class="site-header">
    <div class="brand"><span class="brand-mark"></span>Praxis Lindenhof</div>
    <nav class="main-nav">
      <a href="#" style="left:348px">Praxis</a>
      <a href="#" class="is-active">Leistungen</a>
      <a href="#" style="left:533px">Ärzte</a>
      <a href="#" style="left:603px">Teams</a>
      <a href="#" style="left:678px">Öffnungszeiten</a>
      <a href="#" style="left:808px">Kontakt</a>
    </nav>
  </header>

  <main>
    <h1 class="page-title">Leistungen</h1>
    <ul class="services">
      <li class="service">Gesundheitsvorsorge/Prävention/ Gesundheits-Check-up</li>
      <li class="service">Impfungen und Reiseimpfungen</li>
      <li class="service is-open">Männervorsorge
        <p class="service-body">Sed velit congue viverra. Sed porta mattis luctus. Curabitur feugiat pharetra sem eu iaculis. Phasellus venenatis volutpat arcu id placerat. Aliquam fringilla ligula eu purus lacinia at volutpat nunc malesuada. Nunc a augue ac orci tempus commodo.</p>
      </li>
      <li class="service">Diabetes mellitus</li>
      <li class="service">Psychosomatische Grundversorgung</li>
      <li class="service">Koronare Herzerkrankung (KHK)</li>
      <li class="service">Asthma Bronchiale</li>
      <li class="service">Palliativversorgung</li>
      <li class="service">Prävention</li>
      <li class="service">Echokardiografie</li>
      <li class="service">Sonographische Untersuchung der Schilddrüse</li>
      <li class="service">Check-up“-Laboruntersuchungen sowie PSA-Wert und andere Tumormarker</li>
      <li class="service">EKG und Belastungs-EKG</li>
      <li class="service">Langzeit-Blutdruckmessung</li>
      <li class="service">Lungenfunktionstest</li>
      <li class="service">Disease-Management-Programme (DMP)</li>
      <li class="service">Ultraschall der Bauchorgane</li>
      <li class="service">Ultraschall der Hirnversorgenden Arterien (Duplexsonografie)</li>
      <li class="service">Spiroergometrie</li>
    </ul>
  </main>
  <div class="page-end"></div>
</body>
</html>
```